Dental Medical History Form - Content provided

Design a medical history form for a dental practice. Content is provided so all that is needed is the formatting to make it look great and easy to read.

"Patient Information" to include all information contained in top portion of the "Patient Medical History Form" docx file.

"Medical History" should follow the formatting and content of the "Exact Medical History" file as this is what the entry fields look like in our practice software and so we would like it to match.

1st page - Patient info, allergies, medications, antibiotics, joint replacement, pregnancy.

2nd page - Do you have, or have you had, any of the following? . . . . . . .
Updates

Target Market(s)

All ages but must be clear enough for elderly to read. Use as much space as possible to keep font size bigger yet keep to two pages

Industry/Entity Type

Dental

Font styles to use
Sans Serif

Requirements
Must have
• All content provided
• Our logo at the top (file provided)
• Century Gothic Font
• Limit to two pages

```html
<!DOCTYPE html>
<html lang="en">
<head>
<meta charset="utf-8">
<title>Lumen Dental – Confidential Medical History</title>
<link rel="stylesheet" href="https://fonts.googleapis.com/css2?family=Montserrat:wght@400;500;600;700&display=swap">
<style>
:root{
  --ink:#2b2b2e;
  --rule:#3a3a3d;
  --border:#b9b9bd;
  --accent:#4a4a4f;
  --bar:#3b3c40;
  --paper:#ffffff;
}
*{box-sizing:border-box;margin:0;padding:0}
html,body{width:849px;height:1200px;overflow:hidden;background:var(--paper)}
body{font-family:"Montserrat",sans-serif;color:var(--ink);font-size:12px;position:relative}
.page{position:relative;width:849px;height:1200px}

/* header */
.brand{position:absolute;left:48px;top:46px;display:flex;align-items:center;gap:10px}
.brand-mark{width:16px;height:16px;border-radius:50%;background:var(--accent);flex:none}
.brand-name{font-size:30px;font-weight:500;line-height:1;color:var(--accent)}
.contact{position:absolute;left:575px;top:22px;font-size:11px;line-height:1.25}
.contact-row{display:flex;align-items:center;gap:10px;margin-bottom:6px}
.contact-row svg{width:14px;height:14px;flex:none}

.title{position:absolute;left:0;right:0;top:158px;text-align:center;font-size:17px;font-weight:700;letter-spacing:0.3px}
.title-rule{position:absolute;left:48px;right:48px;top:188px;border-top:1.5px solid var(--rule)}

/* form fields */
.col{position:absolute;top:215px}
.col-left{left:48px;width:360px}
.col-right{left:442px;width:360px}
.field{display:flex;align-items:flex-end;height:22px;font-weight:600;font-size:12px;white-space:nowrap}
.line{flex:1;border-bottom:1px solid var(--rule);margin-left:4px;height:14px}
.sub{display:flex;font-size:10.5px;font-weight:600;height:20px;align-items:flex-start;padding-top:3px}
.gap{height:10px}
.gap-lg{height:26px}

/* option boxes */
.box{position:absolute;left:48px;right:48px;border:1px solid var(--border);border-radius:6px;padding:14px 16px}
.box-allergy{top:512px;height:122px}
.box-meds{top:655px;height:112px}
.box-detail{top:788px;height:120px}
.box-questions{top:928px;height:200px}
.q{font-size:12px;font-weight:600;display:flex;align-items:center;gap:6px;margin-bottom:18px}
.tick{width:16px;height:16px;border-radius:50%;background:var(--accent);display:inline-flex;align-items:center;justify-content:center}
.options{display:flex;flex-wrap:wrap;align-items:center;column-gap:12px;row-gap:14px;font-size:11.5px;font-weight:600}
.opt{display:inline-flex;align-items:center;gap:5px}
.radio{width:14px;height:14px;border:1.2px solid var(--rule);border-radius:50%;display:inline-block}
.other{display:flex;align-items:flex-end;margin-top:16px;font-size:11.5px;font-weight:600}
.detail-lines{display:grid;grid-template-columns:repeat(3,1fr);column-gap:30px;row-gap:12px;margin-top:8px}
.detail-lines span{border-bottom:1px solid var(--rule);height:12px}
.yn{display:flex;align-items:center;gap:8px;font-size:12px;font-weight:600;margin-bottom:20px}

/* footer */
.footer{position:absolute;left:0;right:0;bottom:0;height:34px;background:var(--bar);color:#fff;font-size:11px;display:flex;align-items:center;justify-content:flex-end;padding-right:48px}
</style>
</head>
<body>
<div class="page">

  <header>
    <div class="brand">
      <span class="brand-mark"></span>
      <span class="brand-name">Lumen Dental</span>
    </div>
    <div class="contact">
      <div class="contact-row">
        <svg viewBox="0 0 24 24"><path fill="#2b2b2e" d="M12 2a7 7 0 0 0-7 7c0 5 7 13 7 13s7-8 7-13a7 7 0 0 0-7-7zm0 9.5A2.5 2.5 0 1 1 12 6.5a2.5 2.5 0 0 1 0 5z"/></svg>
        <span>4/118 Harbour View Rd<br>Seacliff NSW 2260</span>
      </div>
      <div class="contact-row">
        <svg viewBox="0 0 24 24"><path fill="#2b2b2e" d="M6.6 10.8a15 15 0 0 0 6.6 6.6l2.2-2.2a1 1 0 0 1 1-.25 11.4 11.4 0 0 0 3.6.57 1 1 0 0 1 1 1V20a1 1 0 0 1-1 1A17 17 0 0 1 3 4a1 1 0 0 1 1-1h3.5a1 1 0 0 1 1 1c0 1.25.2 2.45.57 3.57a1 1 0 0 1-.25 1z"/></svg>
        <span>(02) 40 555 018</span>
      </div>
      <div class="contact-row">
        <svg viewBox="0 0 24 24"><path fill="#2b2b2e" d="M3 4l18 8-18 8 3-8zm3 8h8"/></svg>
        <span>www.lumendental.com.au</span>
      </div>
    </div>
  </header>

  <h1 class="title">CONFIDENTIAL MEDICAL HISTORY</h1>
  <div class="title-rule"></div>

  <section class="col col-left">
    <div class="field">Name:<span class="line"></span></div>
    <div class="sub"><span style="width:70px">Title</span><span style="width:90px">First</span><span style="width:100px">Middle</span><span>Last</span></div>
    <div class="field">Address:<span class="line"></span></div>
    <div class="field"><span class="line" style="margin-left:0"></span></div>
    <div class="field">DOB:<span class="line"></span></div>
    <div class="field">Email Address:<span class="line"></span></div>
    <div class="field">Phone Number(s):<span class="line"></span></div>
    <div class="sub"><span style="width:150px"></span><span style="width:70px">Mobile</span><span style="width:60px">Work</span><span>Home</span></div>
    <div class="field">Emergency Contact Person:</div>
    <div class="field">Name:<span class="line"></span></div>
    <div class="field">Relationship:<span class="line"></span></div>
    <div class="field">Phone number:<span class="line"></span></div>
  </section>

  <section class="col col-right">
    <div class="field">General Practitioner:</div>
    <div class="field">Name:<span class="line"></span></div>
    <div class="field">Practice Name:<span class="line"></span></div>
    <div class="field">Phone Number:<span class="line"></span></div>
    <div class="gap-lg"></div>
    <div class="field">Do you have a health fund with dental cover? Yes or No</div>
    <div class="field">If so, what is the name of the fund?<span class="line"></span></div>
    <div class="field">Fund Number?<span class="line"></span></div>
    <div class="field">Priority Number on card: 0&nbsp; 1&nbsp; 2&nbsp; 3&nbsp; 4&nbsp; 5</div>
    <div class="gap"></div>
    <div class="field">Occupation:<span class="line"></span></div>
    <div class="field">Referred by:<span class="line"></span></div>
  </section>

  <section class="box box-allergy">
    <p class="q">Please indicate if you are allergic to any of the following <span class="tick"><svg width="10" height="10" viewBox="0 0 10 10"><path d="M1.5 5.2l2.3 2.3L8.5 2.5" stroke="#fff" stroke-width="1.6" fill="none"/></svg></span> ?</p>
    <div class="options">
      <span class="opt">Aspirin<span class="radio"></span></span>
      <span class="opt">Codeine<span class="radio"></span></span>
      <span class="opt">Penicillin<span class="radio"></span></span>
      <span class="opt">Sulfites<span class="radio"></span></span>
      <span class="opt">Latex<span class="radio"></span></span>
      <span class="opt">Local Anaesthetic<span class="radio"></span></span>
      <span class="opt">Lactose<span class="radio"></span></span>
      <span class="opt">Nickel<span class="radio"></span></span>
    </div>
    <div class="other">Other:<span class="line"></span></div>
  </section>

  <section class="box box-meds">
    <p class="q">Are you currently taking, or have ever taken, any of the following medication <span class="tick"><svg width="10" height="10" viewBox="0 0 10 10"><path d="M1.5 5.2l2.3 2.3L8.5 2.5" stroke="#fff" stroke-width="1.6" fill="none"/></svg></span> ?</p>
    <div class="options">
      <span class="opt">Asthma Inhaler<span class="radio"></span></span>
      <span class="opt">Anti-epileptics<span class="radio"></span></span>
      <span class="opt">Anti-depressants<span class="radio"></span></span>
      <span class="opt">Blood Pressure<span class="radio"></span></span>
      <span class="opt">Blood Thinners<span class="radio"></span></span>
    </div>
    <div class="options" style="margin-top:14px">
      <span class="opt">Bisphosphonates<span class="radio"></span></span>
      <span class="opt">Chemotherapy<span class="radio"></span></span>
      <span class="opt">Insulin<span class="radio"></span></span>
      <span class="opt">Immunosuppressants<span class="radio"></span></span>
      <span class="opt">Steroids<span class="radio"></span></span>
      <span class="opt">Oral Contraceptive<span class="radio"></span></span>
    </div>
  </section>

  <section class="box box-detail">
    <p class="q" style="margin-bottom:4px">Please specify medication name, dose, and frequency where possible:</p>
    <div class="detail-lines">
      <span></span><span></span><span></span>
      <span></span><span></span><span></span>
      <span></span><span></span><span></span>
    </div>
  </section>

  <section class="box box-questions">
    <p class="yn">Do you require antibiotic cover? Yes <span class="radio"></span> No <span class="radio"></span></p>
    <p class="yn">Have you had a joint replacement? Yes <span class="radio"></span> No <span class="radio"></span></p>
    <p class="yn" style="margin-bottom:8px">Women:</p>
    <p class="yn">Are you pregnant? Yes <span class="radio"></span> No <span class="radio"></span>&nbsp;&nbsp; Possible or Breast Feeding? Yes <span class="radio"></span> No <span class="radio"></span></p>
  </section>

  <footer class="footer">Please Turnover</footer>
</div>
</body>
</html>
```